Brell Stone Company Business Cards

Front and Back Business Card - logo and text setup - cool design. I need workable photoshop or illustrator files so I can setup each employee card with design that is created
Updates

Hi everyone, thank you for the great entries. Please no more white and blue cards - there are so many already - black and silver only now please. thanks!

Target Market(s)

Construction Industry - Facility Managers

Industry/Entity Type

Construction

Contact Information for Business Card

I really like contemporary simplistic looks - clean neat....not opposed to seeing some black backrounds

Requirements
Must have
• Logo/website address with design on front only - www.brellstone-example.com (logo attached)
• Back:
• Name/Title/Company Address/Phone/email address
Nice to have
• Cool design
Should not have
• Nothing gimmicky like Fire or Water - since we are a Fire Protection company - it has all been done

```html
<!DOCTYPE html>
<html lang="en">
<head>
<meta charset="utf-8">
<title>Brell Stone Company Business Cards</title>
<link rel="stylesheet" href="https://fonts.googleapis.com/css2?family=Source+Sans+3:wght@400;700&display=swap">
<style>
  :root {
    --bg: #c9ccd0;
    --ink-black: #000000;
    --brand-blue: #0323a0;
    --brand-red: #ff2222;
    --white: #ffffff;
  }
  html, body {
    margin: 0;
    padding: 0;
    width: 1200px;
    height: 1193px;
    overflow: hidden;
    background: var(--bg);
    font-family: "Source Sans 3", Arial, sans-serif;
  }
  .canvas { position: relative; width: 1200px; height: 1193px; }
  .card { position: absolute; display: block; }
  .card--contact { left: 251px; top: 71px; width: 873px; height: 499px; }
  .card--brand { left: 100px; top: 627px; width: 872px; height: 499px; }
  .card text { font-family: "Source Sans 3", Arial, sans-serif; }
</style>
</head>
<body>
<main class="canvas">

  <svg class="card card--contact" viewBox="0 0 1050 600" role="img" aria-label="Contact side of business card">
    <defs>
      <clipPath id="contact-shape"><rect width="1050" height="600" rx="48"/></clipPath>
    </defs>
    <g clip-path="url(#contact-shape)">
      <rect class="card-base" width="1050" height="600" fill="var(--ink-black)"/>
      <path class="wave-blue" d="M0 360 C60 500 200 530 330 520 C560 505 800 430 1050 415 L1050 600 L0 600 Z" fill="var(--brand-blue)"/>
      <path class="wave-black" d="M0 395 C70 505 210 535 330 530 C560 518 800 450 1050 432 L1050 600 L0 600 Z" fill="var(--ink-black)"/>
      <path class="wave-red" d="M0 405 C70 512 210 540 330 535 C560 523 800 455 1050 440" fill="none" stroke="var(--brand-red)" stroke-width="5"/>
      <path class="wave-base" d="M0 420 C70 525 210 548 330 543 C560 533 800 465 1050 450 L1050 600 L0 600 Z" fill="var(--brand-blue)"/>
    </g>

    <text class="company-name" x="528" y="150" text-anchor="middle" font-size="86" font-weight="700" fill="var(--brand-red)">Brell Stone</text>

    <text class="person" x="525" y="282" text-anchor="middle" fill="var(--white)" font-size="36"><tspan font-weight="700">Mara Ellison,</tspan> <tspan font-weight="400">President</tspan></text>

    <g class="contact-phone">
      <path d="M420 333 l6 -3 l5 8 l-4 3 c2 5 5 8 10 11 l3 -4 l8 5 l-3 6 c-12 2 -27 -13 -25 -26 z" fill="var(--brand-blue)"/>
      <text x="458" y="350" fill="var(--white)" font-size="26">(555) 014-2378</text>
    </g>

    <g class="contact-email">
      <rect x="140" y="381" width="28" height="19" fill="var(--brand-blue)"/>
      <path d="M140 381 l14 11 l14 -11 M140 400 l10 -9 M168 400 l-10 -9" stroke="var(--ink-black)" stroke-width="2" fill="none"/>
      <text x="178" y="398" fill="var(--white)" font-size="26">info@brellstone-example.com</text>
    </g>

    <g class="contact-web">
      <circle cx="556" cy="390" r="14" fill="none" stroke="var(--brand-blue)" stroke-width="2.5"/>
      <ellipse cx="556" cy="390" rx="6" ry="14" fill="none" stroke="var(--brand-blue)" stroke-width="2"/>
      <path d="M542 390 h28 M545 382 h22 M545 398 h22" stroke="var(--brand-blue)" stroke-width="2"/>
      <text x="580" y="398" fill="var(--white)" font-size="26">www.brellstone-example.com</text>
    </g>

    <text class="address" x="525" y="576" text-anchor="middle" fill="var(--white)" font-size="31">48 Harbor Works Lane, Millbrook, NY 10000</text>
  </svg>

  <svg class="card card--brand" viewBox="0 0 1050 600" role="img" aria-label="Brand side of business card">
    <rect class="card-base" width="1050" height="600" rx="48" fill="var(--brand-blue)"/>
    <text class="company-name" x="525" y="320" text-anchor="middle" font-size="104" font-weight="700" fill="var(--white)">Brell Stone</text>
    <text class="website" x="525" y="425" text-anchor="middle" font-size="32" letter-spacing="5" fill="var(--white)">www.brellstone-example.com</text>
  </svg>

</main>
</body>
</html>
```